Heritage Hollow Business Cards

Require a business card design. <br/><br/>Needs to include logo (either round or long version) plus these details:<br/>Maya Torvell<br/>Heritage Hollow<br/>maya@kelvadtrading.com.au<br/>02 6481 7395<br/>PO Box Glenwarra NSW 2791<br/>www.heritagehollow.com.au<br/><br/>I need in an editable format so that I can create for multiple staff members. <br/><br/>

Target Market(s)

We are an online store selling renovation products to home owners are builders. Looking for a classic classy design.

Industry/Entity Type

Home And Garden

Contact Information for Business Card

Maya Torvell
Heritage Hollow
maya@kelvadtrading.com.au
02 6481 7395
PO Box Glenwarra NSW 2791
www.heritagehollow.com.au

Colors

Designer to choose colors to be used in the design.

Requirements
Must have
• Must include Logo.

```html
<!DOCTYPE html>
<html lang="en">
<head>
<meta charset="utf-8">
<title>Heritage Hollow Business Cards</title>
<link href="https://fonts.googleapis.com/css2?family=Work+Sans:wght@400;600&display=swap" rel="stylesheet">
<style>
  :root {
    --page: #e9e9e9;
    --card-dark: #161616;
    --card-light: #2c2c2c;
    --ink: #ffffff;
    --ink-muted: #8a8a8a;
    --ring: rgba(255,255,255,0.75);
  }
  * { margin: 0; padding: 0; box-sizing: border-box; }
  html, body {
    width: 1200px; height: 900px; overflow: hidden;
    background: var(--page);
    font-family: "Work Sans", sans-serif;
    color: var(--ink);
  }
  .sheet {
    position: relative; width: 1200px; height: 900px;
  }
  .card {
    position: absolute; left: 250px; width: 700px; height: 400px;
    background: linear-gradient(135deg, var(--card-dark) 0%, var(--card-dark) 45%, var(--card-light) 100%);
    box-shadow: 0 6px 18px rgba(0,0,0,0.25);
  }
  .card--front { top: 35px; }
  .card--back { top: 465px; }

  .brand-mark {
    position: absolute; width: 230px; height: 230px;
    border: 1px solid var(--ring); border-radius: 50%;
    display: flex; align-items: center; justify-content: center;
    text-align: center;
  }
  .brand-mark__name {
    font-size: 34px; font-weight: 400; line-height: 1.05; color: var(--ink);
  }
  .card--front .brand-mark { left: 290px; top: 55px; }
  .card--back .brand-mark { left: 70px; top: 75px; }

  .front-url {
    position: absolute; left: 0; right: 0; top: 318px;
    text-align: center; padding-left: 60px;
    font-size: 17px; letter-spacing: 0.24em;
  }

  .details {
    position: absolute; left: 370px; top: 80px;
    font-size: 19px; line-height: 1.3;
  }
  .details__name {
    font-size: 31px; font-weight: 600; letter-spacing: 0.06em; line-height: 1.1;
  }
  .details__role { font-size: 17px; margin-bottom: 18px; }
  .details__company { color: var(--ink-muted); margin-bottom: 14px; }
  .details__address { margin-bottom: 18px; }
  .muted { color: var(--ink-muted); }
</style>
</head>
<body>
<main class="sheet">
  <section class="card card--front" aria-label="Card front">
    <div class="brand-mark"><span class="brand-mark__name">Heritage<br>Hollow</span></div>
    <p class="front-url">www.heritagehollow.com.au</p>
  </section>

  <section class="card card--back" aria-label="Card back">
    <div class="brand-mark"><span class="brand-mark__name">Heritage<br>Hollow</span></div>
    <div class="details">
      <p class="details__name">Maya Torvell</p>
      <p class="details__role">Director</p>
      <p class="details__company">Heritage Hollow</p>
      <p class="details__address">PO Box<br>Glenwarra NSW 2791</p>
      <p>02 6481 7395</p>
      <p>maya@kelvadtrading.com.au</p>
      <p>www.<span class="muted">heritagehollow</span>.com.au</p>
    </div>
  </section>
</main>
</body>
</html>
```